Veltrane Group Business Card Design

The CEO is looking for a new trendy look for his business card.
You can stay with current branding or come up with something new/creative. It can be 3D, including Medical Office buildings. You can use our logo in a variety of colors. Please include name, title, company name, company website, email address, cell number

Target Market(s)

Real Estate Development and Construction

Industry/Entity Type

Health care real estate

Contact Information for Business Card

Rohesh Kamdar, CEO M-604.781.2249 E-roheshkamdar@veltrane.com Address:4180 Lindqvist Ave, Tampa, FL 33482 www.veltrane.com

Font styles to use
Other font styles liked:
• Be creative

Requirements
Must have
• Creative, trendy look
Nice to have
• Please go to our website to get a feel- www. veltrane.com
Should not have
• small fonts

```html
<!DOCTYPE html>
<html lang="en">
<head>
<meta charset="utf-8">
<title>Veltrane Group Business Card</title>
<link rel="stylesheet" href="https://fonts.googleapis.com/css2?family=Arimo:wght@400;700&display=swap">
<style>
  :root {
    --backdrop: #b01e2a;
    --card-dark-1: #353535;
    --card-dark-2: #1b1b1b;
    --card-light: #ffffff;
    --brand-red: #b3202b;
    --navy: #1f3157;
    --ink: #1a1a1a;
    --sketch-1: #f4f4f4;
    --sketch-2: #e6e6e6;
  }
  * { margin: 0; padding: 0; box-sizing: border-box; }
  html, body { width: 1200px; height: 1000px; overflow: hidden; }
  body {
    background: var(--backdrop);
    font-family: "Arimo", Arial, sans-serif;
    position: relative;
  }
  .card {
    position: absolute;
    left: 203px;
    width: 794px;
    height: 453px;
    border-radius: 28px;
    overflow: hidden;
  }
  .card--front {
    top: 30px;
    background: radial-gradient(ellipse at 45% 25%, var(--card-dark-1) 0%, var(--card-dark-2) 85%);
    display: flex;
    align-items: center;
    justify-content: center;
  }
  .front-wordmark {
    display: flex;
    align-items: center;
    gap: 18px;
    color: var(--brand-red);
    font-weight: 700;
    font-size: 60px;
    letter-spacing: 1px;
  }
  .front-wordmark .mark-dot {
    width: 44px; height: 44px; border-radius: 50%;
    background: var(--brand-red);
  }
  .card--back {
    top: 508px;
    background: var(--card-light);
  }
  .building-sketch {
    position: absolute;
    left: 0; top: 0;
    width: 340px; height: 100%;
    background: linear-gradient(90deg, var(--sketch-1) 0%, var(--sketch-2) 55%, var(--card-light) 100%);
  }
  .identity {
    position: absolute;
    left: 400px;
    top: 62px;
  }
  .identity .name {
    color: var(--brand-red);
    font-weight: 700;
    font-size: 35px;
    letter-spacing: 0.5px;
    line-height: 1;
  }
  .identity .title {
    color: var(--navy);
    font-weight: 700;
    font-size: 20px;
    margin-top: 8px;
  }
  .contacts {
    position: absolute;
    left: 402px;
    top: 170px;
    list-style: none;
  }
  .contacts li {
    display: flex;
    align-items: flex-start;
    gap: 10px;
    color: var(--ink);
    font-size: 20px;
    line-height: 24px;
    margin-bottom: 8px;
  }
  .contacts svg { width: 20px; height: 22px; flex: 0 0 20px; margin-top: 1px; fill: var(--navy); }
  .back-wordmark {
    position: absolute;
    right: 30px;
    bottom: 36px;
    color: var(--brand-red);
    font-weight: 700;
    font-size: 32px;
  }
</style>
</head>
<body>
  <section class="card card--front">
    <div class="front-wordmark"><span class="mark-dot"></span>Veltrane Group</div>
  </section>

  <section class="card card--back">
    <div class="building-sketch" role="img" aria-label="Faint line drawing of a tall medical office building"></div>

    <div class="identity">
      <div class="name">ROHESH KAMDAR</div>
      <div class="title">CEO</div>
    </div>

    <ul class="contacts">
      <li>
        <svg viewBox="0 0 20 22" aria-hidden="true"><path d="M5 1h10a2 2 0 0 1 2 2v16a2 2 0 0 1-2 2H5a2 2 0 0 1-2-2V3a2 2 0 0 1 2-2zm0 2v13h10V3zm5 14.5a1 1 0 1 0 0 2 1 1 0 0 0 0-2z"/></svg>
        <span>M-604.781.2249</span>
      </li>
      <li>
        <svg viewBox="0 0 20 22" aria-hidden="true"><path d="M19 3 1 10l6 2.5L16 6l-7 7.5V19l3.2-3.8L16 18z"/></svg>
        <span>roheshkamdar@veltrane.com</span>
      </li>
      <li>
        <svg viewBox="0 0 20 22" aria-hidden="true"><path d="M10 2a9 9 0 1 0 0 18 9 9 0 0 0 0-18zm0 2c.9 0 2 1.8 2.4 5H7.6C8 5.8 9.1 4 10 4zM5.6 9H3.2a7 7 0 0 1 4-4.6C6.4 5.6 5.8 7.2 5.6 9zm0 2c.2 1.8.8 3.4 1.6 4.6a7 7 0 0 1-4-4.6zm2 0h4.8c-.4 3.2-1.5 5-2.4 5s-2-1.8-2.4-5zm6.8 0h2.4a7 7 0 0 1-4 4.6c.8-1.2 1.4-2.8 1.6-4.6zm0-2c-.2-1.8-.8-3.4-1.6-4.6a7 7 0 0 1 4 4.6z"/></svg>
        <span>www.veltrane.com</span>
      </li>
      <li>
        <svg viewBox="0 0 20 22" aria-hidden="true"><path d="M10 1a7 7 0 0 0-7 7c0 5 7 13 7 13s7-8 7-13a7 7 0 0 0-7-7zm0 9.5A2.5 2.5 0 1 1 10 5.5a2.5 2.5 0 0 1 0 5z"/></svg>
        <span>4180 Lindqvist Ave, Tampa,<br>FL 33482</span>
      </li>
    </ul>

    <div class="back-wordmark">Veltrane Group</div>
  </section>
</body>
</html>
```